CAMBRAI CELEBRATES ANDOUILETTE

On the occasion of the big annual sale, in CAMBRAI, the 57th celebrates the Cambrai specialty "andouillette de CAMBRAI".

On this occasion, we are developing a special menu for this day;

- Authentic CAMBRAI sausage, old-fashioned mustard sauce, served with fresh fries cooked in beef fat and green salad
- CAMBRAI andouillette salad (lettuce, tomatoes, onions, CAMBRAI andouillette, Tome de CAMBRAI, Cambrai apples
- Andouillette gratin (Homemade mash, CAMBRAI andouillette, old-fashioned mustard, gratin with CAMBRAI tome
- BRUSCHETTA: Cream base, CAMBRAI sausage, CAMBRAI tome, onions, old-fashioned mustard
- Grilled ham
- Fried mussels, with CAMBRAI tome cream

The event will take place on Sunday July 2, in continuous service.

Please write in French, and insert the logo of the establishment of 57 and illustrate well.

THANKS

```html
<!DOCTYPE html>
<html lang="fr">
<head>
<meta charset="utf-8">
<title>Le 57 — Cambrai Celebrates Andouillette</title>
<link href="https://fonts.googleapis.com/css2?family=Ultra&family=Poppins:wght@400;500;600&family=Playfair+Display:wght@700&display=swap" rel="stylesheet">
<style>
:root{
  --bg:#ebebea;
  --board:#262625;
  --board-edge:#1d1d1c;
  --gold:#d4a73a;
  --gold-light:#f1cd63;
  --gold-dark:#a97e1f;
  --ink:#ffffff;
  --muted:#d9d9d9;
  --dark:#222;
}
*{margin:0;padding:0;box-sizing:border-box}
html,body{width:1200px;height:3187px;overflow:hidden;background:var(--bg)}
.poster{
  position:absolute;left:50px;top:814px;width:1100px;height:1559px;
  background:linear-gradient(180deg,#2b2b2a,var(--board) 50%,var(--board-edge));
  box-shadow:0 30px 50px rgba(0,0,0,.35);
  font-family:'Poppins',sans-serif;color:var(--ink);
}
.abs{position:absolute}
.center{left:0;right:0;text-align:center}
.rule{position:absolute;background:var(--gold);height:2px}
.vrule{position:absolute;background:var(--gold);width:2px}
.ornament{position:absolute;width:210px;height:210px;border-radius:40%;
  background:radial-gradient(circle,rgba(212,167,58,.55),rgba(212,167,58,.08) 70%,transparent)}
.sketch{position:absolute;border-radius:50%;
  background:radial-gradient(circle,rgba(200,200,200,.14),rgba(200,200,200,.03) 70%,transparent)}
.brand{top:130px;left:440px;width:220px;height:190px;display:flex;align-items:center;justify-content:center;gap:14px}
.brand-dot{width:26px;height:26px;border-radius:50%;background:var(--gold)}
.brand-name{font-family:'Poppins',sans-serif;font-weight:500;font-size:58px;color:var(--ink);line-height:1}
.kicker{top:348px;font-size:20px;letter-spacing:7px;font-weight:500}
.gold-text{background:linear-gradient(180deg,var(--gold-light),var(--gold) 55%,var(--gold-dark));
  -webkit-background-clip:text;background-clip:text;color:transparent}
.title{top:378px;font-family:'Ultra',serif;font-size:100px;line-height:1.1}
.subtitle{top:490px;font-family:'Ultra',serif;font-size:44px;line-height:1.1}
.sub-rule{left:182px;width:735px}
.occasion{left:142px;top:575px;width:813px;height:200px;border:3px solid var(--gold);outline:2px solid #555;outline-offset:4px}
.occasion h2{position:absolute;top:28px;left:0;right:0;text-align:center;font-size:31px;font-weight:600;letter-spacing:1.5px}
.occasion h3{position:absolute;top:66px;left:0;right:0;text-align:center;font-family:'Ultra',serif;font-size:30px;font-weight:400}
.occasion .cols{position:absolute;top:130px;left:38px;right:30px;display:flex;font-size:17px;line-height:1.3}
.occasion .cols p{padding-right:18px;margin-right:18px;border-right:1px solid #888}
.occasion .cols p:last-child{border:0}
.when{top:808px;font-size:24px;letter-spacing:4px}
.ribbon{left:175px;top:842px;width:750px;height:76px}
.date{top:847px;font-family:'Ultra',serif;font-size:48px;color:var(--dark)}
.service{top:927px;font-size:26px;font-weight:600;letter-spacing:2px}
.tab{position:absolute;background:#fff;color:var(--dark);font-family:'Playfair Display',serif;font-weight:700;font-size:20px;padding:4px 24px;white-space:nowrap}
.dish{position:absolute;border:2px solid var(--gold);font-size:18px;display:flex;flex-direction:column;justify-content:center;gap:6px}
.dish .row{display:flex;justify-content:center;gap:34px}
.tag{position:absolute;border:2px solid var(--gold);outline:1px solid #666;outline-offset:3px;font-family:'Playfair Display',serif;font-weight:700;font-size:21px;padding:6px 16px;color:var(--muted)}
.url{top:1412px;font-size:21px;font-weight:600;letter-spacing:6px}
.url span{color:var(--gold)}
</style>
</head>
<body>
<main class="poster">
  <div class="rule" style="left:300px;top:87px;width:500px"></div>
  <div class="rule" style="left:300px;top:1475px;width:500px"></div>
  <div class="vrule" style="left:75px;top:300px;height:1080px"></div>
  <div class="vrule" style="left:1023px;top:300px;height:1080px"></div>

  <div class="ornament" role="img" aria-label="Ornement doré en volutes, coin supérieur gauche" style="left:40px;top:55px"></div>
  <div class="ornament" role="img" aria-label="Ornement doré en volutes, coin supérieur droit" style="right:40px;top:55px"></div>
  <div class="ornament" role="img" aria-label="Ornement doré en volutes, coin inférieur gauche" style="left:40px;bottom:55px"></div>
  <div class="ornament" role="img" aria-label="Ornement doré en volutes, coin inférieur droit" style="right:40px;bottom:55px"></div>

  <div class="sketch" role="img" aria-label="Dessin au trait d'une poêle et d'ingrédients" style="left:100px;top:150px;width:300px;height:260px"></div>
  <div class="sketch" role="img" aria-label="Dessin au trait d'un plat d'andouillette avec frites et sauce" style="left:690px;top:170px;width:330px;height:230px"></div>
  <div class="sketch" role="img" aria-label="Dessin au trait de pain" style="left:110px;top:1250px;width:120px;height:120px"></div>
  <div class="sketch" role="img" aria-label="Dessin au trait d'un croissant" style="left:870px;top:1240px;width:120px;height:120px"></div>

  <div class="abs brand">
    <span class="brand-dot"></span><span class="brand-name">le 57</span>
  </div>

  <p class="abs center kicker">LE 57 FÊTE LA SPÉCIALITÉ CAMBRAI</p>
  <h1 class="abs center title"><span class="gold-text">CAMBRAI</span></h1>
  <div class="rule sub-rule" style="top:492px"></div>
  <p class="abs center subtitle"><span class="gold-text">CELEBRATES ANDOUILETTE</span></p>
  <div class="rule sub-rule" style="top:548px"></div>

  <section class="abs occasion">
    <h2>A L'OCCASION DE LA GRANDE VENTE ANNUELLE</h2>
    <h3><span class="gold-text">◀ NOTRE MENU SPÉCIAL ▶</span></h3>
    <div class="cols">
      <p>Authentique<br>CAMBRAI Saucisse</p>
      <p>Démodé<br>Sauce moutarde</p>
      <p>Servi avec frites fraîches cuites<br>dans Gras de Boeuf et Salade Verte</p>
    </div>
  </section>

  <p class="abs center when">L'ÉVÉNEMENT AURA LIEU LE</p>
  <svg class="abs ribbon" viewBox="0 0 750 76" aria-hidden="true">
    <defs><linearGradient id="goldband" x1="0" y1="0" x2="0" y2="1">
      <stop offset="0" stop-color="#f1cd63"/><stop offset=".55" stop-color="#d4a73a"/><stop offset="1" stop-color="#a97e1f"/>
    </linearGradient></defs>
    <polygon points="0,0 750,0 720,38 750,76 0,76 30,38" fill="url(#goldband)"/>
    <polyline points="40,6 62,38 40,70" fill="none" stroke="#262625" stroke-width="2"/>
    <polyline points="710,6 688,38 710,70" fill="none" stroke="#262625" stroke-width="2"/>
  </svg>
  <p class="abs center date">DIMANCHE 2 JUILLET</p>
  <div class="rule" style="left:315px;top:945px;width:65px"></div>
  <div class="rule" style="left:720px;top:945px;width:65px"></div>
  <p class="abs center service">EN SERVICE CONTINU</p>

  <div class="dish" style="left:228px;top:1037px;width:644px;height:75px">
    <div class="row"><span>Laitue</span><span>Tomates</span><span>Tome de CAMBRAI</span></div>
    <div class="row"><span>CAMBRAI andouillette</span><span>Pommes de Cambrai</span><span>Oignons</span></div>
  </div>
  <span class="tab" style="left:387px;top:1006px">CAMBRAI Andouillette Salad</span>

  <div class="dish" style="left:228px;top:1163px;width:644px;height:75px">
    <div class="row"><span>Purée maison</span><span>CAMBRAI andouillette</span></div>
    <div class="row"><span>Moutarde à l'ancienne</span><span>Gratin au tome CAMBRAI</span></div>
  </div>
  <span class="tab" style="left:468px;top:1132px">Andouillette Gratin</span>

  <span class="tag" style="left:255px;top:1270px">BRUSCHETTA</span>
  <div class="abs" style="left:455px;top:1270px;font-size:18px;line-height:1.5">
    <div style="display:flex;gap:32px"><span>Base crème</span><span>Saucisse CAMBRAI</span><span>Oignons</span></div>
    <div style="display:flex;gap:38px"><span>Tome CAMBRAI</span><span>Moutarde à l'ancienne</span></div>
  </div>

  <span class="tag" style="left:238px;top:1348px">GRILLED HAM</span>
  <div class="dish" style="left:455px;top:1348px;width:395px;height:44px;font-size:17px">
    <div class="row"><span>MOULES FRITES</span><span>TOME CRÈME CAMBRAI</span></div>
  </div>

  <p class="abs center url">www.<span>le57-bistrot</span>.fr</p>
</main>
</body>
</html>
```